Corporate Business Card

Very professional, Modern, Not to busy, include phone address email, website
(555) 617-4930, 18761 52nd Avenue S, Harlow, ID 98047, martin@plumlinegroup.com, varkoworks.com

Target Market(s)

Manufacturing

Industry/Entity Type

Aero, machining, manufacturing, Off road racing

Contact Information for Business Card

Phone, address email, website

```html
<!DOCTYPE html>
<html lang="en">
<head>
<meta charset="utf-8">
<title>Varko Works – Business Card</title>
<link href="https://fonts.googleapis.com/css2?family=Roboto:wght@400;500;700;900&display=swap" rel="stylesheet">
<style>
  :root {
    --navy: #24356b;
    --red: #c3202a;
    --card: #efefef;
    --backdrop: #2a2a2a;
    --ink: #1f2a55;
  }
  * { margin: 0; padding: 0; box-sizing: border-box; }
  html, body { width: 1200px; height: 1138px; overflow: hidden; }
  body {
    background: var(--backdrop);
    font-family: "Roboto", sans-serif;
    position: relative;
  }
  .card {
    position: absolute;
    left: 275px;
    width: 622px;
    height: 375px;
    background: var(--card);
    border-radius: 14px;
    overflow: hidden;
  }
  .card-front { top: 186px; }
  .card-back { top: 608px; }

  /* Front */
  .front-wordmark {
    position: absolute;
    top: 118px; left: 0; right: 0;
    text-align: center;
    font-weight: 900;
    font-size: 58px;
    line-height: 72px;
    letter-spacing: 2px;
    color: var(--navy);
  }
  .front-rule {
    position: absolute; left: 106px; top: 221px;
    width: 410px; height: 2px; background: var(--navy);
  }
  .front-web {
    position: absolute;
    top: 326px; left: 0; right: 0;
    display: flex; justify-content: center; align-items: center; gap: 18px;
    font-size: 16px; color: #222;
  }
  .front-web .dash { width: 70px; height: 2px; background: var(--red); }
  .front-band {
    position: absolute; left: 0; right: 0; bottom: 0; height: 10px;
    display: flex;
  }
  .front-band .navy { flex: 1; background: var(--navy); }
  .front-band .red { flex: 1; background: var(--red); }

  /* Back */
  .holder-name {
    position: absolute; left: 36px; top: 88px;
    font-weight: 700; font-size: 30px; line-height: 34px; letter-spacing: 0.5px;
    color: var(--navy);
  }
  .holder-name .surname { color: var(--red); }
  .name-rule {
    position: absolute; left: 36px; top: 129px;
    width: 422px; height: 2px; background: var(--navy);
  }
  .back-wordmark {
    position: absolute; right: 40px; top: 72px;
    font-weight: 900; font-size: 34px; line-height: 44px; letter-spacing: 1px;
    color: var(--navy);
  }
  .contact-list {
    position: absolute; left: 36px; top: 270px;
    list-style: none;
  }
  .contact-list li {
    display: flex; align-items: center; gap: 16px;
    height: 24px; font-size: 17px; color: var(--ink);
  }
  .contact-list svg { width: 16px; height: 16px; fill: var(--red); }
  .address {
    position: absolute; right: 68px; top: 295px;
    text-align: right; font-size: 17px; line-height: 24px; color: var(--ink);
  }
  .address-pin {
    position: absolute; right: 36px; top: 298px;
    width: 14px; height: 18px; fill: var(--red);
  }
</style>
</head>
<body>

<section class="card card-front">
  <div class="front-wordmark">VARKO WORKS</div>
  <div class="front-rule"></div>
  <div class="front-web">
    <span class="dash"></span>
    <span>www.varkoworks.com</span>
    <span class="dash"></span>
  </div>
  <div class="front-band"><span class="navy"></span><span class="red"></span></div>
</section>

<section class="card card-back">
  <div class="holder-name">MARTIN <span class="surname">HALE</span></div>
  <div class="name-rule"></div>
  <div class="back-wordmark">VARKO WORKS</div>

  <ul class="contact-list">
    <li>
      <svg viewBox="0 0 24 24" aria-hidden="true"><path d="M6.6 10.8a15.1 15.1 0 0 0 6.6 6.6l2.2-2.2a1 1 0 0 1 1-.25 11.4 11.4 0 0 0 3.6.57 1 1 0 0 1 1 1V20a1 1 0 0 1-1 1A17 17 0 0 1 3 4a1 1 0 0 1 1-1h3.5a1 1 0 0 1 1 1c0 1.25.2 2.45.57 3.57a1 1 0 0 1-.25 1z"/></svg>
      <span>(555) 617-4930</span>
    </li>
    <li>
      <svg viewBox="0 0 24 24" aria-hidden="true"><path d="M2 5h20v14H2z M4 7v.4l8 5.2 8-5.2V7l-8 5.2z" fill-rule="evenodd"/></svg>
      <span>martin@plumlinegroup.com</span>
    </li>
    <li>
      <svg viewBox="0 0 24 24" aria-hidden="true"><path d="M12 2a10 10 0 1 0 0 20 10 10 0 0 0 0-20zm0 2c1 1.2 1.8 3 2.1 5H9.9C10.2 7 11 5.2 12 4zM4.3 11h3.6c.05.7.1 1.4.25 2H4.3a8 8 0 0 1 0-2zm5.6 0h4.2a14 14 0 0 1-.2 2h-3.8a14 14 0 0 1-.2-2zm6.2 0h3.6a8 8 0 0 1 0 2h-3.85c.15-.6.2-1.3.25-2zM12 20c-1-1.2-1.8-3-2.1-5h4.2c-.3 2-1.1 3.8-2.1 5z"/></svg>
      <span>www.varkoworks.com</span>
    </li>
  </ul>

  <div class="address">18761 52nd Avenue S,<br>Harlow, ID 98047</div>
  <svg class="address-pin" viewBox="0 0 14 18" aria-hidden="true"><path d="M7 0a7 7 0 0 0-7 7c0 5 7 11 7 11s7-6 7-11a7 7 0 0 0-7-7zm0 4a3 3 0 1 1 0 6 3 3 0 0 1 0-6z" fill-rule="evenodd"/></svg>
</section>

</body>
</html>
```